New iOS App design for Boston Startup

We are looking for a new app design for our iPhone app. The current app's design feels outdated and we like to add lots of new functionality and a new navigation as well. A complete overhaul therefore!
We want you to design 5 screens that will have changed the most. The complete wireframes of these 5 pages are attached in the requirements document.
Once the winning design is selected we will award the winner with the designing all other screens (40-50 screens based on the same design). This will be a separate project worth $1000. The winning designer can get more follow up work if both sides are happy about the cooperation.
We will give feedback as soon as the first screen has been uploaded for review. Final decision will be made only after all 5 screens are finished.
We hope you give it your best!
Note: will only communicate through PixelHarbor (no skype),
Updates
Reason: Want to give designers a chance to submit their designs as I understand from some, the deadline is too close.
I have raised the award and introduced a 2nd price as well to make it worth your time. I hope you give it your best shot.
Reason: A few of you have asked for an extension of the deadline as time is running out. I will extend by one day. Tell me if you need more.
Industry/Entity Type
Startup
Requirements
Must have
- At least 1 screen before we can give you feedback.
Nice to have
- multiple options of 1 screen to get to a desirable design

```html
<!DOCTYPE html>
<html lang="en">
<head>
<meta charset="utf-8">
<title>Home screen variations</title>
<link rel="stylesheet" href="https://fonts.googleapis.com/css2?family=Lato:wght@300;400;700&family=Arimo:wght@400;700&display=swap">
<style>
  :root {
    --canvas: #b4b9be;
    --screen: #232323;
    --screen-dark: #1c1c1c;
    --band: #363636;
    --tabbar: #282828;
    --accent: #1eb2d8;
    --accent-text: #22a9d6;
    --white: #ffffff;
    --muted: #8d8d8d;
    --muted-dark: #6a6a6a;
    --rise: #2fd36a;
    --fall: #ef4a4a;
    --rule: #cfcfcf;
  }
  * { box-sizing: border-box; margin: 0; padding: 0; }
  html, body { width: 1200px; height: 1000px; overflow: hidden; }
  body {
    position: relative;
    background: var(--canvas);
    font-family: "Lato", "Helvetica Neue", Arial, sans-serif;
  }
  .icon-library { position: absolute; width: 0; height: 0; }

  .screen {
    position: absolute;
    width: 380px;
    height: 568px;
    background: var(--screen);
    overflow: hidden;
    color: var(--white);
  }
  .screen--today { left: 18px; top: 228px; }
  .screen--week { left: 413px; top: 193px; }
  .screen--inline { left: 805px; top: 158px; }

  .app-header { position: absolute; left: 0; top: 0; width: 100%; height: 62px; }
  .menu-button { position: absolute; left: 24px; top: 19px; width: 24px; height: 20px; }
  .menu-button span { display: block; height: 4px; background: var(--white); margin-bottom: 4px; }
  .app-title {
    position: absolute; left: 0; right: 0; top: 10px; text-align: center;
    font-weight: 300; font-size: 33px; letter-spacing: -0.5px;
  }

  .welcome-band {
    position: absolute; left: 8px; right: 0; top: 68px; height: 64px;
    background: linear-gradient(180deg, #3b3b3b, #313131);
  }
  .welcome-greeting { position: absolute; left: 17px; top: 5px; font-size: 15px; color: var(--accent-text); font-weight: 400; }
  .welcome-name { position: absolute; left: 15px; top: 16px; font-size: 36px; font-weight: 300; color: var(--accent-text); letter-spacing: -0.5px; }
  .score-label { position: absolute; left: 222px; top: 9px; font-size: 10px; color: var(--white); letter-spacing: 0.3px; }
  .score-value { position: absolute; left: 220px; top: 16px; font-size: 38px; font-weight: 400; letter-spacing: -1px; }
  .score-trend { position: absolute; left: 295px; top: 27px; width: 16px; height: 22px; }
  .score-delta { position: absolute; left: 325px; top: 28px; font-size: 22px; }

  .stats { position: absolute; left: 0; width: 100%; }
  .screen--today .stats, .screen--week .stats { top: 150px; height: 90px; }
  .screen--inline .stats { top: 160px; height: 58px; }
  .stats-period { text-align: center; font-size: 17px; color: var(--accent-text); height: 28px; }
  .stats-row { position: relative; height: 52px; }
  .stats-arrow { position: absolute; top: 14px; width: 14px; height: 22px; }
  .stats-arrow--prev { left: 14px; }
  .stats-arrow--next { right: 6px; }
  .stats-viewport {
    position: absolute; left: 34px; width: 320px; top: 0; height: 52px; overflow: hidden;
    border-right: 1px solid #9a9a9a;
  }
  .stats-track { position: absolute; left: -16px; top: 0; display: flex; }
  .screen--inline .stats-track { left: -2px; }
  .stat { width: 118px; text-align: center; }
  .stat-leading { width: 58px; text-align: left; padding-top: 14px; font-size: 19px; color: var(--accent-text); }
  .stat-name { font-family: "Arimo", Arial, sans-serif; font-weight: 700; font-size: 15px; color: var(--accent-text); line-height: 20px; }
  .stat-value {
    font-family: "Arimo", Arial, sans-serif; font-weight: 700; font-size: 20px; color: var(--muted);
    white-space: nowrap; line-height: 26px;
  }
  .stat-value svg { width: 11px; height: 15px; vertical-align: -1px; margin: 0 1px; }
  .stats-rule { position: absolute; left: 14px; right: 4px; bottom: 0; height: 1px; background: var(--rule); }

  .shortcuts {
    position: absolute; left: 16px; right: 0; height: 70px;
    background: #202020; border-bottom: 1px solid #181818;
    display: flex;
  }
  .screen--today .shortcuts, .screen--week .shortcuts { top: 246px; }
  .screen--inline .shortcuts { top: 226px; }
  .shortcut { flex: 1; text-align: center; padding-top: 10px; font-size: 12.5px; color: var(--muted); }
  .shortcut svg { display: block; margin: 0 auto 3px; width: 36px; height: 32px; }
  .shortcut--active { color: var(--accent-text); }
  .shortcut-count { display: block; font-size: 25px; color: var(--accent-text); height: 34px; line-height: 32px; }

  .up-next { position: absolute; left: 0; right: 0; text-align: center; }
  .screen--today .up-next, .screen--week .up-next { top: 340px; }
  .screen--inline .up-next { top: 340px; }
  .up-next-label { font-size: 20px; color: var(--muted); font-weight: 400; margin-bottom: 12px; }
  .lesson-button {
    display: block; margin-left: 17px; width: 355px; height: 44px; line-height: 44px;
    background: var(--accent); color: var(--white); font-size: 20px; text-align: center;
  }

  .tab-bar {
    position: absolute; left: 0; right: 0; bottom: 0; height: 68px;
    background: var(--tabbar); border-top: 1px solid #333; display: flex;
  }
  .tab { flex: 1; text-align: center; font-size: 11px; color: var(--muted-dark); padding-top: 8px; position: relative; }
  .tab svg { display: block; margin: 0 auto 3px; width: 34px; height: 32px; }
  .tab--active { color: var(--accent-text); }
  .tab--active::before {
    content: ""; position: absolute; left: 0; right: 0; top: -2px; height: 2px; background: var(--accent);
  }
</style>
</head>
<body>

<svg class="icon-library" aria-hidden="true">
  <defs>
    <symbol id="icon-trend-down" viewBox="0 0 16 22"><path d="M5 0h6v12h5L8 22 0 12h5z" fill="#ef4a4a"/></symbol>
    <symbol id="icon-trend-up" viewBox="0 0 11 15"><path d="M3.5 15V7H0L5.5 0 11 7H7.5v8z" fill="#2fd36a"/></symbol>
    <symbol id="icon-chevron-left" viewBox="0 0 14 22"><path d="M11 2 3 11l8 9" fill="none" stroke="#1eb2d8" stroke-width="3.5"/></symbol>
    <symbol id="icon-chevron-right" viewBox="0 0 14 22"><path d="M3 2l8 9-8 9" fill="none" stroke="#1eb2d8" stroke-width="3.5"/></symbol>
    <symbol id="icon-analytics" viewBox="0 0 36 32">
      <g fill="#1eb2d8"><rect x="4" y="13" width="8" height="15"/><rect x="14" y="3" width="8" height="25"/><rect x="24" y="16" width="8" height="12"/><rect x="2" y="29" width="32" height="2"/></g>
    </symbol>
    <symbol id="icon-course" viewBox="0 0 36 32">
      <g fill="none" stroke="#8d8d8d" stroke-width="1.4"><path d="M7 2h16v28H7z"/><path d="M10 8h10M10 12h9M10 16h7M10 20h8M10 24h10"/><circle cx="24" cy="14" r="5"/><path d="M27.5 17.5l5 5"/></g>
    </symbol>
    <symbol id="icon-theory" viewBox="0 0 34 32">
      <g fill="none" stroke="#6a6a6a" stroke-width="1.6"><path d="M2 5c5-2 10-2 15 1 5-3 10-3 15-1v22c-5-2-10-2-15 1-5-3-10-3-15-1z"/><path d="M17 6v22"/></g>
    </symbol>
    <symbol id="icon-practice" viewBox="0 0 34 32">
      <g fill="none" stroke="#6a6a6a" stroke-width="1.3"><rect x="3" y="1" width="28" height="30"/><path d="M17 1v30M3 16h28"/></g>
      <g fill="#6a6a6a" font-family="Arial, sans-serif" font-size="11" text-anchor="middle"><text x="10" y="12">a</text><text x="24" y="12">b</text><text x="10" y="27">c</text><text x="24" y="27">d</text></g>
    </symbol>
    <symbol id="icon-home" viewBox="0 0 34 32"><path d="M17 1 1 15h5v16h8v-9h6v9h8V15h5z" fill="#1eb2d8"/></symbol>
    <symbol id="icon-games" viewBox="0 0 34 32">
      <g fill="none" stroke="#6a6a6a" stroke-width="1.6"><path d="M9 9h16c5 0 8 9 8 14 0 4-4 5-7 1l-3-3H11l-3 3c-3 4-7 3-7-1 0-5 3-14 8-14z"/><path d="M9 13v6M6 16h6"/><circle cx="23" cy="14" r="1"/><circle cx="26" cy="17" r="1"/></g>
    </symbol>
    <symbol id="icon-tests" viewBox="0 0 34 32">
      <g fill="none" stroke="#6a6a6a" stroke-width="1.6"><path d="M6 4h18v27H6z"/><path d="M9 12h10M9 16h10M9 20h10M9 24h10"/><path d="M28 2l3 3-12 12-4 1 1-4z"/></g>
    </symbol>
  </defs>
</svg>

<!-- Screen A: period label above the stats -->
<section class="screen screen--today">
  <header class="app-header">
    <div class="menu-button"><span></span><span></span><span></span></div>
    <h1 class="app-title">Home</h1>
  </header>
  <div class="welcome-band">
    <p class="welcome-greeting">welcome back,</p>
    <p class="welcome-name">OREN</p>
    <p class="score-label">SCORE</p>
    <p class="score-value">650</p>
    <svg class="score-trend"><use href="#icon-trend-down"/></svg>
    <p class="score-delta">-18</p>
  </div>
  <div class="stats">
    <p class="stats-period">Today</p>
    <div class="stats-row">
      <svg class="stats-arrow stats-arrow--prev"><use href="#icon-chevron-left"/></svg>
      <div class="stats-viewport">
        <div class="stats-track">
          <div class="stat"><p class="stat-name">Completion</p><p class="stat-value">34%<svg><use href="#icon-trend-up"/></svg>+4</p></div>
          <div class="stat"><p class="stat-name">Sessions</p><p class="stat-value">20<svg><use href="#icon-trend-up"/></svg>+3</p></div>
          <div class="stat"><p class="stat-name">Min.</p><p class="stat-value">18<svg><use href="#icon-trend-up"/></svg>+10</p></div>
        </div>
      </div>
      <svg class="stats-arrow stats-arrow--next"><use href="#icon-chevron-right"/></svg>
    </div>
    <div class="stats-rule"></div>
  </div>
  <nav class="shortcuts">
    <div class="shortcut shortcut--active"><svg><use href="#icon-analytics"/></svg>Analytics</div>
    <div class="shortcut"><svg><use href="#icon-course"/></svg>Course Overview</div>
    <div class="shortcut"><span class="shortcut-count">33</span>Days until test</div>
  </nav>
  <div class="up-next">
    <p class="up-next-label">Up Next:</p>
    <a class="lesson-button">Lesson 4 - Sentence Correction</a>
  </div>
  <nav class="tab-bar">
    <div class="tab"><svg><use href="#icon-theory"/></svg>Theory</div>
    <div class="tab"><svg><use href="#icon-practice"/></svg>Practice</div>
    <div class="tab tab--active"><svg><use href="#icon-home"/></svg>Home</div>
    <div class="tab"><svg><use href="#icon-games"/></svg>Games</div>
    <div class="tab"><svg><use href="#icon-tests"/></svg>Tests</div>
  </nav>
</section>

<!-- Screen B: weekly period -->
<section class="screen screen--week">
  <header class="app-header">
    <div class="menu-button"><span></span><span></span><span></span></div>
    <h1 class="app-title">Home</h1>
  </header>
  <div class="welcome-band">
    <p class="welcome-greeting">welcome back,</p>
    <p class="welcome-name">OREN</p>
    <p class="score-label">SCORE</p>
    <p class="score-value">650</p>
    <svg class="score-trend"><use href="#icon-trend-down"/></svg>
    <p class="score-delta">-18</p>
  </div>
  <div class="stats">
    <p class="stats-period">This Week</p>
    <div class="stats-row">
      <svg class="stats-arrow stats-arrow--prev"><use href="#icon-chevron-left"/></svg>
      <div class="stats-viewport">
        <div class="stats-track">
          <div class="stat"><p class="stat-name">Completion</p><p class="stat-value">34%<svg><use href="#icon-trend-up"/></svg>+4</p></div>
          <div class="stat"><p class="stat-name">Sessions</p><p class="stat-value">20<svg><use href="#icon-trend-up"/></svg>+3</p></div>
          <div class="stat"><p class="stat-name">Min.</p><p class="stat-value">18<svg><use href="#icon-trend-up"/></svg>+10</p></div>
        </div>
      </div>
      <svg class="stats-arrow stats-arrow--next"><use href="#icon-chevron-right"/></svg>
    </div>
    <div class="stats-rule"></div>
  </div>
  <nav class="shortcuts">
    <div class="shortcut shortcut--active"><svg><use href="#icon-analytics"/></svg>Analytics</div>
    <div class="shortcut"><svg><use href="#icon-course"/></svg>Course Overview</div>
    <div class="shortcut"><span class="shortcut-count">33</span>Days until test</div>
  </nav>
  <div class="up-next">
    <p class="up-next-label">Up Next:</p>
    <a class="lesson-button">Lesson 4 - Sentence Correction</a>
  </div>
  <nav class="tab-bar">
    <div class="tab"><svg><use href="#icon-theory"/></svg>Theory</div>
    <div class="tab"><svg><use href="#icon-practice"/></svg>Practice</div>
    <div class="tab tab--active"><svg><use href="#icon-home"/></svg>Home</div>
    <div class="tab"><svg><use href="#icon-games"/></svg>Games</div>
    <div class="tab"><svg><use href="#icon-tests"/></svg>Tests</div>
  </nav>
</section>

<!-- Screen C: period inline with the stats -->
<section class="screen screen--inline">
  <header class="app-header">
    <div class="menu-button"><span></span><span></span><span></span></div>
    <h1 class="app-title">Home</h1>
  </header>
  <div class="welcome-band">
    <p class="welcome-greeting">welcome back,</p>
    <p class="welcome-name">OREN</p>
    <p class="score-label">SCORE</p>
    <p class="score-value">650</p>
    <svg class="score-trend"><use href="#icon-trend-down"/></svg>
    <p class="score-delta">-18</p>
  </div>
  <div class="stats">
    <div class="stats-row">
      <svg class="stats-arrow stats-arrow--prev"><use href="#icon-chevron-left"/></svg>
      <div class="stats-viewport">
        <div class="stats-track">
          <div class="stat-leading">Today</div>
          <div class="stat"><p class="stat-name">Completion</p><p class="stat-value">34%<svg><use href="#icon-trend-up"/></svg>+4</p></div>
          <div class="stat"><p class="stat-name">Sessions</p><p class="stat-value">20<svg><use href="#icon-trend-up"/></svg>+3</p></div>
          <div class="stat"><p class="stat-name">Min.</p><p class="stat-value">18<svg><use href="#icon-trend-up"/></svg>+10</p></div>
        </div>
      </div>
      <svg class="stats-arrow stats-arrow--next"><use href="#icon-chevron-right"/></svg>
    </div>
    <div class="stats-rule"></div>
  </div>
  <nav class="shortcuts">
    <div class="shortcut shortcut--active"><svg><use href="#icon-analytics"/></svg>Analytics</div>
    <div class="shortcut"><svg><use href="#icon-course"/></svg>Course Overview</div>
    <div class="shortcut"><span class="shortcut-count">33</span>Days until test</div>
  </nav>
  <div class="up-next">
    <p class="up-next-label">Up Next:</p>
    <a class="lesson-button">Lesson 4 - Sentence Correction</a>
  </div>
  <nav class="tab-bar">
    <div class="tab"><svg><use href="#icon-theory"/></svg>Theory</div>
    <div class="tab"><svg><use href="#icon-practice"/></svg>Practice</div>
    <div class="tab tab--active"><svg><use href="#icon-home"/></svg>Home</div>
    <div class="tab"><svg><use href="#icon-games"/></svg>Games</div>
    <div class="tab"><svg><use href="#icon-tests"/></svg>Tests</div>
  </nav>
</section>

</body>
</html>
```